Hardcore nerd needs to stand out in a sea of dull Defence business cards

Wombarra Devices is a new Australian consulting engineering company that turns research and theory into practical systems. No evangelistic fluff, just mathematics and physics into electronic and optical circuits for consumer products, scientific research or Defence applications.

We already have a recognised logo (provided) which is often dark blue/black on a light background but we're open to other combinations. (Us engineers tend to have limited aesthetic imagination :)

Some of our recent products have included:
* Instrumentation for electrical testing,
* Radar jammers,
* GPS antenna design,
* Satellite tracking systems,
* High power lasers

We're open to both single and double-sided designs - happy to be convinced either way.

P.S. Another group is working on the web page, so - alas - our web site is currently of no use for images/ideas...

Target Market(s)

Engineering managers,
Scientists

Contact Information for Business Card

Dr Colin Harte
R&D Engineer

colin@wombarradevices.com.au
0427 563 710

PO Box XXX (to be confirmed)
Kelsby ACT 2917
Australia

Font styles to use
Serif
Sans Serif

Colors

Designer to choose colors to be used in the design.

Requirements
Must have
• My contact details!
• I've had many (great) "bold and plain" designs submitted already, so feel free to be artistically creative :)
• Happy to take advice re fonts/colours/printability etc.
Nice to have
• I'm not sure if "lists" are more at home on a CV than a business card, but representative services include:
• Applied electromagnetics
• RF and high speed electronics
• Signal and image processing
• Electro-optical and laser systems
• Concept-to-prototype design services
• If you're considering double sided cards, then often measuring/alignment grids/rulers feature on the back of similar cards.
• e.g. https://www.veltranoptics.example/newgrouppage9.cfm?objectgroup_id=4183
• https://www.veltranoptics.example/newgrouppage9.cfm?objectgroup_ID=4185
• ..or even a "Smith chart" (google will return lots)
• Generic images to represent a capability might work - googling images associated with keyword for each of these areas might help:
• - "passive radar", "phased array", "fdtd", "vircator"
• RF and high speed electronic design
• - "smith chart", "microstrip circuits", "dimensioned drawing", "electronic schematic"
• - "dft", "iir filter"
• - "optical cavity". "laser energy level diagram"
• Background/watermarked images outlines/wireframes/schematics would probably look OK.
Should not have
• If a list of projects/services is provided, it is important not to make the client feel that this is "all" the company can do. Engineering design is a creative discipline (like graphics :)
• Please, no stock "military" snaps like planes, missiles, etc!

```html
<!DOCTYPE html>
<html lang="en">
<head>
<meta charset="utf-8">
<title>Wombarra Devices — Business Card</title>
<link href="https://fonts.googleapis.com/css2?family=Lato:wght@400;700;900&display=swap" rel="stylesheet">
<style>
  :root {
    --backdrop: #2b2b2e;
    --navy: #232a5e;
    --paper: #ffffff;
    --ink: #3a3a44;
    --rule: #b9bccb;
  }
  * { box-sizing: border-box; margin: 0; padding: 0; }
  html, body {
    width: 1200px; height: 970px; overflow: hidden;
    background: var(--backdrop);
    font-family: "Lato", sans-serif;
  }
  .sheet {
    position: relative; width: 1200px; height: 970px;
  }
  .card {
    position: absolute; left: 230px; width: 740px; height: 423px;
    box-shadow: 0 10px 30px rgba(0,0,0,.45);
  }
  .card--front { top: 42px; background: var(--paper); }
  .card--back { top: 505px; background: var(--navy); }

  /* brand lockup */
  .brand { position: absolute; display: flex; align-items: center; gap: 14px; }
  .brand__dot { border-radius: 50%; flex: none; }
  .brand__name {
    font-weight: 900; text-transform: uppercase; line-height: 1.02;
    letter-spacing: .06em;
  }
  .card--front .brand { left: 58px; top: 168px; }
  .card--front .brand__dot { width: 78px; height: 78px; background: var(--navy); }
  .card--front .brand__name { color: var(--navy); font-size: 30px; }

  .divider {
    position: absolute; left: 352px; top: 110px; width: 1px; height: 200px;
    background: var(--rule);
  }

  .contact { position: absolute; left: 392px; top: 112px; color: var(--ink); }
  .contact__name { color: var(--navy); font-weight: 900; font-size: 27px; line-height: 1.1; }
  .contact__role { font-size: 15px; margin-top: 2px; }
  .contact__address { font-size: 15px; line-height: 1.35; margin-top: 10px; }
  .contact__list { list-style: none; margin-top: 10px; font-size: 15px; }
  .contact__list li { display: flex; align-items: center; gap: 10px; line-height: 1.55; }
  .contact__list svg { width: 14px; height: 14px; fill: var(--navy); flex: none; }

  .card--back .brand { left: 170px; top: 78px; }
  .card--back .brand__dot { width: 96px; height: 96px; background: var(--paper); }
  .card--back .brand__name { color: var(--paper); font-size: 37px; }

  .capabilities {
    position: absolute; left: 200px; top: 218px; list-style: none;
    color: var(--paper); font-size: 23px;
  }
  .capabilities li { display: flex; align-items: center; gap: 14px; line-height: 1.42; }
  .capabilities li::before {
    content: ""; width: 13px; height: 13px; border-radius: 50%;
    background: var(--paper); flex: none;
  }
</style>
</head>
<body>
<main class="sheet">
  <section class="card card--front">
    <div class="brand">
      <span class="brand__dot"></span>
      <span class="brand__name">Wombarra<br>Devices</span>
    </div>
    <div class="divider"></div>
    <div class="contact">
      <p class="contact__name">Dr Colin Harte</p>
      <p class="contact__role">R&amp;D Engineer</p>
      <p class="contact__address">PO Box XXX<br>Kelsby ACT 2917, Australia</p>
      <ul class="contact__list">
        <li><svg viewBox="0 0 24 24" aria-hidden="true"><path d="M6.6 10.8a15 15 0 0 0 6.6 6.6l2.2-2.2c.3-.3.7-.4 1-.2 1.1.4 2.3.6 3.6.6.6 0 1 .4 1 1V20c0 .6-.4 1-1 1A17 17 0 0 1 3 4c0-.6.4-1 1-1h3.5c.6 0 1 .4 1 1 0 1.3.2 2.5.6 3.6.1.3 0 .7-.2 1z"/></svg>0427 563 710</li>
        <li><svg viewBox="0 0 24 24" aria-hidden="true"><path d="M2 5h20v14H2zm2 2v.4l8 5.3 8-5.3V7zm0 2.8V17h16V9.8l-8 5.3z"/></svg>colin@wombarradevices.com.au</li>
        <li><svg viewBox="0 0 24 24" aria-hidden="true"><path d="M12 2a10 10 0 1 0 0 20 10 10 0 0 0 0-20zm6.9 6h-3a15 15 0 0 0-1.3-3.9A8 8 0 0 1 18.9 8zM12 4c.8 1.2 1.5 2.5 1.9 4h-3.8c.4-1.5 1.1-2.8 1.9-4zM4.3 14a8 8 0 0 1 0-4h3.4a16 16 0 0 0 0 4zm.8 2h3a15 15 0 0 0 1.3 3.9A8 8 0 0 1 5.1 16zm3-8h-3a8 8 0 0 1 4.3-3.9C8.8 5.3 8.4 6.6 8.1 8zM12 20c-.8-1.2-1.5-2.5-1.9-4h3.8c-.4 1.5-1.1 2.8-1.9 4zm2.3-6H9.7a14 14 0 0 1 0-4h4.6a14 14 0 0 1 0 4zm.3 5.9c.6-1.2 1-2.5 1.3-3.9h3a8 8 0 0 1-4.3 3.9zm1.7-5.9a16 16 0 0 0 0-4h3.4a8 8 0 0 1 0 4z"/></svg>www.wombarradevices.com.au</li>
      </ul>
    </div>
  </section>

  <section class="card card--back">
    <div class="brand">
      <span class="brand__dot"></span>
      <span class="brand__name">Wombarra<br>Devices</span>
    </div>
    <ul class="capabilities">
      <li>Instrumentation for electrical testing</li>
      <li>Radar jammers</li>
      <li>GPS antenna design</li>
      <li>Satellite tracking systems</li>
      <li>High power lasers</li>
    </ul>
  </section>
</main>
</body>
</html>
```